San Francisco Leading Consulting firm - 47Vora Web Design Project

•Create a Web Design
•Uncoded webpage layout design
•2 Pages Design - Homepage + Interior Page

Task Description
Hello, we're looking for a re-design our current website www.47vora-example.com

we have a sample mockup design @

http://47vora.pubtrellis-example.org/

This shows the layout that we like and also a sample of 6 pictures that would change based on where you mouse over..

6 pictures HOME design needs to be included.

SMART
THOUGHTFUL
FLEXIBLE
CREATIVE SERVICES
TECHNICAL SERVICES
PARTNERS

sites we like:

http://www.melvanadvisory-example.com/Home.cfm?id=Home
http://www.plinthworks-example.com/index.html

Our company can be best described as: 100+ employees, cutting-edge, depandable, innovative, strong, smart.

Our Primary focus is: IT Consulting Services and Creative Design services

47Vora LLC is a consulting firm providing creative design, business and technology solutions to both private and public interests.

Established in 1996, 47Vora is a San Francisco based company providing specialists for a range of business needs including:

Creative Design Services
•Print
•Logo Design
•Website Design
•Illustration

and

Business and Technology solutions

•Application Software and Web Development
•Business Process Re-Design (BPR)
•Business/Systems Analysis and Requirement Documentation
•Mentoring and Training
•Network/Hardware Installation Services
•System Design and Architecture
•Vendor Management
•Docuvault Architecture and Implementation

our sample mockup site:

Reason: Due to holiday season, we're not available to work with designers and finilize our design.  

Thank you very much for submitting your design.

We appreciate your time and creativity.   Since, our office is currently closed for holidays, we will be reviewing it in details next week and will make our decision as soon as possible.

It would be great if you could submit any of your changes by Wed next week, so it would be part of our reviews. 

Please see updated wireframe under attachments:  we have some minor updates to our wireframe that we would like you to update your designs, if possible.  

We also encorouge you not to use our standard wireframe and come up with more unique designs.   Everything would be considered when we review your design.

 

Target Market(s)

Creative services and professional services clients, including government agencies

Industry/Entity Type

Business

Requirements
Must have
• Clean, professional look, easy navigation

```html
<!DOCTYPE html>
<html lang="en">
<head>
<meta charset="utf-8">
<title>47Vora — Home</title>
<link rel="stylesheet" href="https://fonts.googleapis.com/css2?family=Ubuntu:wght@300;400;500;700&family=Didact+Gothic&family=Open+Sans:wght@400;600;700&display=swap">
<style>
:root{
  --page:#ececec;
  --frame:#dcdcdc;
  --panel:#f4f4f4;
  --menu:#1f4c70;
  --menu-dark:#173f5f;
  --menu-line:#4f7699;
  --hero-a:#245e8c;
  --hero-b:#4b95c6;
  --accent:#1a5e96;
  --ink:#222;
  --nav:#333;
  --footer:#2f2f2f;
  --footer-top:#1c1c1c;
  --footer-text:#a8a8a8;
  --footer-head:#bcbcbc;
}
*{box-sizing:border-box;margin:0;padding:0}
html,body{width:1200px;height:892px;overflow:hidden}
body{background:var(--page);font-family:"Open Sans",sans-serif}
.stage{position:absolute;left:0;top:0;width:1422px;height:1057px;transform:scale(.84388);transform-origin:0 0;
  background:linear-gradient(#e9e9e9 0,#f2f2f2 500px,#fff 870px)}
.abs{position:absolute}
/* header */
.logo{left:222px;top:30px;display:flex;align-items:center;gap:12px}
.logo-dot{width:44px;height:44px;border-radius:50%;background:#3f8fcf}
.logo-name{font-family:"Ubuntu",sans-serif;font-weight:300;font-size:40px;letter-spacing:2px;color:#444}
.nav{left:590px;top:57px;display:flex;align-items:center;font-family:"Didact Gothic",sans-serif;font-size:15px;color:var(--nav)}
.nav a{color:inherit;text-decoration:none;padding:0 10px;line-height:29px}
.nav .sep{color:#555}
.nav .current{background:repeating-linear-gradient(45deg,#ddd 0 2px,#e6e6e6 2px 4px);color:var(--accent);font-family:"Ubuntu",sans-serif;font-weight:700;font-size:17px;padding:0 12px}
/* main frame */
.frame{left:210px;top:123px;width:1002px;height:753px;background:repeating-linear-gradient(45deg,#d6d6d6 0 2px,#e4e4e4 2px 4px)}
.panel{left:222px;top:135px;width:978px;height:741px;background:linear-gradient(#f0f0f0,#fafafa 500px,#fff)}
/* hero */
.hero{left:222px;top:135px;width:978px;height:341px;background:linear-gradient(100deg,var(--hero-a),var(--hero-b))}
.hero-photo{left:578px;top:40px;width:400px;height:301px;background:linear-gradient(90deg,rgba(80,150,200,0),#b9d4e6 45%,#7ea6c4)}
.menu{left:0;top:0;width:275px;height:341px}
.menu-item{position:absolute;left:0;width:275px;height:56px;background:var(--menu);border-bottom:1px solid var(--menu-line);
  font-family:"Ubuntu",sans-serif;font-weight:500;font-size:24px;color:#fff;display:flex;align-items:center;padding-left:12px;gap:12px}
.menu-item.dark{background:#1a4466}
.chev{font-weight:700;font-size:20px}
.menu-active{position:absolute;left:0;top:171px;width:489px;height:57px;background:var(--menu-dark);
  font-family:"Ubuntu",sans-serif;font-weight:500;font-size:30px;color:#fff;display:flex;align-items:center;justify-content:flex-end;padding-right:14px;gap:18px}
.hero-copy{left:297px;top:232px;width:290px;font-family:"Open Sans",sans-serif;font-weight:700;font-size:12.5px;line-height:14.5px;color:#fff}
.hero-more{left:297px;top:304px;font-weight:700;font-size:11.5px;color:#fff;letter-spacing:.5px}
/* columns */
.col{position:absolute;top:512px;width:281px}
.col-head{height:37px;background:repeating-linear-gradient(45deg,#e0e0e0 0 2px,#ebebeb 2px 4px);font-family:"Ubuntu",sans-serif;font-weight:500;font-size:18px;color:var(--accent);text-align:center;line-height:38px}
.col-pic{margin-top:5px;height:114px;background:#fff;border:1px solid #ddd;padding:5px}
.col-pic div{width:100%;height:100%}
.col h3{margin:24px 0 0 5px;font-size:12.5px;font-weight:700;color:var(--ink);letter-spacing:.3px}
.col p{margin:9px 0 0 5px;width:262px;font-size:12.4px;line-height:14.5px;color:var(--ink)}
.btn{position:absolute;top:274px;left:0;width:124px;height:30px;border:1px solid #c9c9c9;border-radius:9px;background:linear-gradient(#fff,#e8e8e8);
  font-size:12px;font-weight:600;color:#444;text-align:center;line-height:28px}
.vdots{position:absolute;top:518px;height:290px;border-left:1px dotted #bbb}
/* footer */
.footer{left:0;top:876px;width:1422px;height:181px;background:var(--footer);border-top:8px solid var(--footer-top)}
.footer-inner{left:210px;top:884px;width:1002px;height:173px;background:repeating-linear-gradient(45deg,#2c2c2c 0 2px,#343434 2px 4px)}
.t-title{left:228px;top:895px;font-family:"Ubuntu",sans-serif;font-weight:500;font-size:18px;color:var(--footer-head)}
.t-text{left:229px;top:927px;width:525px;font-size:12.4px;line-height:14.3px;color:var(--footer-text)}
.t-name{left:230px;top:999px;font-size:12px;font-weight:700;color:var(--footer-text);letter-spacing:.5px}
.t-role{left:230px;top:1013px;font-size:12.4px;color:var(--footer-text)}
.t-more{left:677px;top:999px;font-size:11.5px;font-weight:700;color:var(--footer-text);letter-spacing:.6px}
.f-rule{left:819px;top:905px;height:110px;border-left:1px solid #444}
.contact{right:241px;top:898px;text-align:right;font-size:12.4px;line-height:14px;color:var(--footer-text);font-style:normal}
.social{left:1032px;top:977px;display:flex;gap:11px}
.social span{width:30px;height:30px;background:#8a8a8a;border-radius:3px}
.copy{right:242px;top:1014px;font-size:12.4px;color:var(--footer-text)}
</style>
</head>
<body>
<div class="stage">
  <header>
    <div class="abs logo"><span class="logo-dot"></span><span class="logo-name">47VORA</span></div>
    <nav class="abs nav">
      <a class="current">Home</a>
      <a>Company</a><span class="sep">|</span>
      <a>Technical Services</a><span class="sep">|</span>
      <a>Creative Services</a><span class="sep">|</span>
      <a>Partners</a><span class="sep">|</span>
      <a>Contact Us</a>
    </nav>
  </header>

  <div class="abs frame"></div>
  <div class="abs panel"></div>

  <section class="abs hero">
    <div class="abs hero-photo" role="img" aria-label="Photo of three business people holding question-mark signs in front of their faces"></div>
    <div class="abs menu">
      <div class="menu-item" style="top:0"><span class="chev">&gt;</span>SMART</div>
      <div class="menu-item" style="top:57px"><span class="chev">&gt;</span>FLEXIBLE</div>
      <div class="menu-item" style="top:114px"><span class="chev">&gt;</span>CREATIVE SERVICES</div>
      <div class="menu-item" style="top:228px"><span class="chev">&gt;</span>TECHNICAL SERVICES</div>
      <div class="menu-item" style="top:285px;height:56px;border-bottom:0"><span class="chev">&gt;</span>PARTNERS</div>
    </div>
    <div class="menu-active"><span class="chev" style="font-size:24px">&raquo;</span>THOUGHTFUL</div>
    <p class="abs hero-copy">Lorem Ipsum is simply dummy text of the printing and typesetting industry. Lorem Ipsum has been the industry's standard dummy text ever since the 1500s.</p>
    <span class="abs hero-more">Read More</span>
  </section>

  <section>
    <article class="col" style="left:238px">
      <h2 class="col-head">FOR GRAPHIC DESIGNERS</h2>
      <div class="col-pic"><div role="img" aria-label="Illustration of a head silhouette filled with gears" style="background:linear-gradient(90deg,#4a3f48,#9a8a4a 45%,#4a3f48)"></div></div>
      <h3>Get Creative!</h3>
      <p>47Vora is looking for top creative talent to deliver graphic design solutions for some leading global brands Do you have what it takes?</p>
      <span class="btn">Read More</span>
    </article>
    <div class="vdots" style="left:545px"></div>
    <article class="col" style="left:574px">
      <h2 class="col-head">FOR CLIENTS</h2>
      <div class="col-pic"><div role="img" aria-label="Image of a glowing globe covered in network lines" style="background:linear-gradient(110deg,#1d6b4a,#2a8fa0 50%,#0a1020)"></div></div>
      <h3>The 47Vora Difference</h3>
      <p>47Vora is looking for top creative talent to deliver graphic design solutions for some leading global brands Do you have what it takes?</p>
      <span class="btn">Read More</span>
    </article>
    <div class="vdots" style="left:878px"></div>
    <article class="col" style="left:906px">
      <h2 class="col-head">FOR PARTNERS</h2>
      <div class="col-pic"><div role="img" aria-label="Photo of many hands stacked together in teamwork" style="background:linear-gradient(90deg,#c9a07e,#e2c3a4 50%,#b88a66)"></div></div>
      <h3>Team Up With the Best</h3>
      <p>47Vora is looking for top creative talent to deliver graphic design solutions for some leading global brands Do you have what it takes?</p>
      <span class="btn">Read More</span>
    </article>
  </section>

  <footer>
    <div class="abs footer"></div>
    <div class="abs footer-inner"></div>
    <h2 class="abs t-title">Testimonials</h2>
    <p class="abs t-text">Now we can start to reap the benefits of current technology, including full vendor support, enhanced financial system functionality, and automation of manual processes. This upgrade was a necessary prerequisite to our full deployment of a strategic systems architecture.....</p>
    <span class="abs t-name">Dana Whitlow</span>
    <span class="abs t-role">Director – IS, Bayview Harbor Authority</span>
    <span class="abs t-more">Read More</span>
    <div class="abs f-rule"></div>
    <address class="abs contact">47Vora, LLC<br>2250 Alder Street, Suite 840<br>San Francisco, CA 94110<br>Phone: 1-415-555-0142<br>Fax: 1-415-555-0178</address>
    <div class="abs social" aria-label="Social links"><span></span><span></span><span></span><span></span></div>
    <p class="abs copy">Copyright 2010, 47Vora, LLC All rights reserved</p>
  </footer>
</div>
</body>
</html>
```